Silver Kite Venture Series Travel Brochure

I'm looking for a brochure design for a new travel product - Silver Kite Venture Series, catering for students above 12 years old. Target audience are schools that do destination projects. Brochure to be read by head teacher, parents and students.

Brochure should be A4 in size, 4-6 pages. Format of brochure is hard cover (a folder) with inlet for flyers. Flyers for destinations will be updated from time to time.

Finished job needs to be converted to electronic format for website and email proposal usage.

Attached is text to be used on brochure. Order of section can be adjusted.

For "Elements of the trip", please understand the contents and explain/display it in a graphic form.

For flyer, please come out with a template that I can use for other destinations. The main elements - what's included, number of days, location for pictures, itinerary, educational focus, should be alterable. Attached are text for two sample destinations.
Also attached (tour itinerary example) a version of flyer that I like.

I'm attaching some pictures here. If you find more suitable pictures, please feel free to use them.

Reason: I'm extending the deadline of this project by 4 days, as I need to add details & photo of another travel specialist in personnel session (total of 3 members). Also, in view of the amount of work a designer has to do for this project, I'm giving you more time for submission. Please do not hesitate to be in touch should you need more than 4 days extension. Thank you.

Target Market(s)

Schools - especially the head teacher and parents, to send students above 12 years old to travel

Industry/Entity Type

Electronic

Requirements
Must have
• This is a travel brochure with education elements in it. Parents feel better when their children are travelling for a purpose and lead by responsible teachers/adults whom they can trust. So, the design has to emphasis that education elements and safety are our utmost priority.
Nice to have
• We specialise in environmental study. So, it is nice to have the environmental touch in the design.
Should not have
• Our target market segment is the Middle East, which can be quite sensitive to religion. I prefer not to have any religious related illustration on the design.

```html
<!DOCTYPE html>
<html lang="en">
<head>
<meta charset="utf-8">
<title>Destination 3 – Egypt</title>
<link href="https://fonts.googleapis.com/css2?family=Alfa+Slab+One&family=Open+Sans:wght@300;400;600;700&display=swap" rel="stylesheet">
<style>
  :root{
    --paper:#ffffff;
    --leaf-green:#8dc63f;
    --stem-green:#3fae49;
    --deep-green:#1f5e22;
    --sky-blue:#5ca6dc;
    --navy:#17385e;
    --title-green:#3da544;
    --ink:#1a1a1a;
    --soft-blue:#3f6fb0;
  }
  *{margin:0;padding:0;box-sizing:border-box}
  html,body{width:864px;height:1200px;overflow:hidden;background:var(--paper)}
  body{font-family:"Open Sans",Arial,sans-serif;color:var(--ink);position:relative}
  .slab{font-family:"Alfa Slab One",Georgia,serif;font-weight:400}

  .photo{position:absolute;left:66px;top:132px;width:246px;height:524px;
    background:linear-gradient(180deg,#c9c2b8 0%,#a98f6f 30%,#8a7258 55%,#5e4a37 80%,#4a3a2b 100%)}
  .destination-label{position:absolute;left:66px;top:446px;width:246px;text-align:center;color:#fff}
  .destination-label .number{font-size:20px;display:block;line-height:1}
  .destination-label .country{font-size:45px;display:block;line-height:1.05;letter-spacing:1px}

  .itinerary{position:absolute;left:312px;top:132px;width:487px;height:276px;background:var(--leaf-green);
    display:grid;grid-template-columns:231px 232px;padding:37px 0 0 24px}
  .itinerary .day{font-size:12.5px;color:var(--deep-green);line-height:1.15;margin-top:1px}
  .itinerary p{font-size:11.6px;line-height:13.4px;color:#10300f}

  .focus{position:absolute;left:312px;top:408px;width:487px;height:159px;background:var(--sky-blue);
    display:grid;grid-template-columns:231px 232px;padding:12px 0 0 24px}
  .focus h2{font-size:16.5px;color:var(--navy);line-height:1.25}
  .focus p{font-size:13.3px;font-weight:600;color:#fff;line-height:16px;margin-bottom:4px}
  .focus .related{max-width:190px}

  .included{position:absolute;left:336px;top:573px;width:463px}
  .included h2{font-size:17px;color:var(--title-green);line-height:1.2;margin-bottom:6px}
  .included ul{list-style:none;display:grid;grid-template-columns:231px 232px;font-size:12.2px;line-height:17.5px}

  .stem-rule{position:absolute;left:309px;top:132px;width:7px;height:536px;background:var(--stem-green);border-radius:0 0 4px 4px}
  .leaf-area{position:absolute;left:286px;top:90px;width:194px;height:72px;
    background:linear-gradient(180deg,#9fd452 0%,#6fb83a 100%)}

  .closing{position:absolute;left:0;top:765px;width:864px;text-align:center;color:var(--soft-blue);
    font-weight:300;font-size:22.5px;line-height:35.5px}

  .contact{position:absolute;left:66px;top:1063px;font-size:10px;line-height:13px;color:var(--ink);font-style:normal}
  .contact strong{font-weight:700}

  .inclusion-icons{position:absolute;left:443px;top:1100px}
</style>
</head>
<body>

  <div class="photo" role="img" aria-label="Photograph of a stone pyramid in the Egyptian desert"></div>
  <div class="destination-label">
    <span class="number slab">Destination 3</span>
    <span class="country slab">EGYPT</span>
  </div>

  <section class="itinerary">
    <div>
      <h3 class="day slab">Day 1</h3>
      <p>Arrival at Cairo<br>Cairo city tour<br>Pyramid and Sphinx</p>
      <h3 class="day slab">Day 2</h3>
      <p>Cairo Museum &amp; Khan El Khalili Bazaar<br>Cairo to Aswan by flight or train</p>
      <h3 class="day slab">Day 3</h3>
      <p>Embark on Nile Cruise<br>Visit high dam, unfinished obelisk,<br>Philae Temple</p>
      <h3 class="day slab">Day 4</h3>
      <p>Nile Cruise<br>Visit Temple of Kom Ombo and<br>Edfu Temple</p>
    </div>
    <div>
      <h3 class="day slab">Day 5</h3>
      <p>Nile Cruise<br>Visit Temple of Karnak and<br>Temple of Luxor</p>
      <h3 class="day slab">Day 6</h3>
      <p>Disembark from Nile Cruise – visit Luxor<br>Colossi of Memnon, Valley of the Kings<br>and Hatshepsut Temple</p>
      <h3 class="day slab">Day 7</h3>
      <p>Luxor visit Collosi of Memnon<br>Valley of the King<br>Hatshepsut Temple<br>Lucor to Cairo by train</p>
      <h3 class="day slab">Day 8</h3>
      <p>Departure</p>
    </div>
  </section>

  <section class="focus">
    <div>
      <h2 class="slab">Main focus subject</h2>
      <p>History and Anthropology</p>
      <h2 class="slab">Related subjects</h2>
      <p class="related">Geography, Development Studies, Agriculture, Environmental Management</p>
    </div>
    <div>
      <h2 class="slab">Environmental focus</h2>
      <p>Impact of climate change on the Nile river basin.</p>
    </div>
  </section>

  <section class="included">
    <h2 class="slab">What's included in price:</h2>
    <ul>
      <li>Air ticket</li><li>Meals</li>
      <li>All accommodation</li><li>Tours led by local expert tour guides</li>
      <li>Full time tour director</li><li>Entrance fees to attractions</li>
    </ul>
  </section>

  <div class="stem-rule" aria-hidden="true"></div>
  <div class="leaf-area" role="img" aria-label="Illustration of a green leaf sprouting above the itinerary panel"></div>

  <p class="closing">Above are some of our more popular destinations.<br>
    With our vast knowledge and expertise in the Middle East, Asia and Europe<br>
    destinations, we are able to cater for other countries not mentioned.<br>
    We are constantly expanding our radar to new destinations. Upcoming<br>
    destinations are Vietnam, Cambodia and Namibia.</p>

  <address class="contact">
    <strong>Harbourline Travel Co.</strong><br>
    Suite 1204, Palm Crest Tower, Marina District,<br>
    PO Box 550120, Dubai, UAE<br>
    <strong>Tel:</strong> +971 4 000 1234<br>
    <strong>Fax:</strong> +971 4 000 5678<br>
    <strong>Email:</strong> hello@harbourline.example
  </address>

  <svg class="inclusion-icons" width="360" height="40" viewBox="0 0 360 40" role="img" aria-label="Inclusion icons: air ticket, accommodation, tour director, meals, local guide, entrance ticket">
    <rect x="0" y="12" width="56" height="24" rx="2" fill="#1a1a1a"/>
    <text x="6" y="28" font-family="Open Sans, Arial, sans-serif" font-weight="700" font-size="9" fill="#fff">TICKET</text>
    <path d="M43 24 h9 M48 20 l4 4 -4 4" stroke="#8dc63f" stroke-width="2" fill="none"/>
    <g fill="none" stroke="#1a1a1a" stroke-width="2.5">
      <path d="M75 14 v24 M120 22 v16 M75 30 h45"/>
    </g>
    <rect x="79" y="20" width="10" height="7" fill="#3fae49"/>
    <rect x="91" y="22" width="27" height="6" fill="#3fae49"/>
    <rect x="138" y="6" width="44" height="32" rx="3" fill="#1a1a1a"/>
    <rect x="196" y="8" width="22" height="30" rx="3" fill="#3fae49"/>
    <rect x="232" y="6" width="44" height="32" rx="3" fill="#3fae49"/>
    <rect x="290" y="12" width="56" height="26" rx="3" fill="#3fae49"/>
    <text x="296" y="23" font-family="Open Sans, Arial, sans-serif" font-weight="700" font-size="7" fill="#1a1a1a">ENTRANCE</text>
    <text x="300" y="33" font-family="Open Sans, Arial, sans-serif" font-weight="700" font-size="9" fill="#1a1a1a">TICKET</text>
  </svg>

</body>
</html>
```